Clearvale glass & hardware manufacturer

Need a SEO friendly, modern & professional looking website. We are selling all kinds of glass & accessories ( Glass/ Mirror/ splash back/ pool fence/ balustrade/ hardware...we are specialised on some special glass, like curve glass,tinted glass thermal & accoustic glass...) It should has simple & crisp feeling like a glass. It must be fully functional with product display and online ordering. Please see attached confirmed logo design(Blue & white). Make sure the theme color match its feel.

Target Market(s)

Architect and designer, Builder, & Developer

Industry/Entity Type

Manufacturer

Coding

Coded - Design and coding required

Font styles to use
Serif
Sans Serif

Colors

Designer to choose colors to be used in the design.

Requirements
Must have
• Glass & hardware theme and our logo
• Here are some competitor's website for reference. (Borrow ideas but not copy : )
• 1.https://www.tarvino.com.au/about
• 2.http://www.plumeretail.com.au/
• 3.http://www.kwd.com.au/
• 4.http://www.brackenhillfittings.com.au/
Nice to have
• Some transparent or semi transparent effects to make the website like a glass
Should not have
• No limitation for your imagination

```html
<!DOCTYPE html>
<html lang="en">
<head>
<meta charset="utf-8">
<title>Clearvale Glass &amp; Hardware</title>
<link rel="stylesheet" href="https://fonts.googleapis.com/css2?family=Open+Sans:wght@400;600;700;800&family=Montserrat:wght@500;600;700&family=Roboto:wght@400;500&display=swap">
<style>
:root{
  --blue:#2a93d5;
  --blue-dark:#1f6fb0;
  --navy:#1c3f7a;
  --ink:#1b1b1b;
  --text:#333;
  --muted:#666;
  --line:#cfcfcf;
  --footer:#e7e7e9;
  --white:#fff;
}
*{box-sizing:border-box;margin:0;padding:0}
html,body{width:1200px;height:2791px;overflow:hidden;background:var(--white)}
body{position:relative;font-family:"Roboto",Arial,sans-serif;color:var(--text)}
.abs{position:absolute}

/* header */
.site-header{position:absolute;left:0;top:0;width:1200px;height:108px;background:var(--white)}
.brand{position:absolute;left:130px;top:28px;display:flex;align-items:center;gap:14px}
.brand-mark{width:46px;height:46px;background:var(--navy)}
.brand-name{font-family:"Open Sans",sans-serif;font-weight:800;font-size:40px;color:var(--navy);letter-spacing:1px}
.call{position:absolute;left:742px;top:20px;display:flex;align-items:center;gap:12px}
.call small{display:block;font-size:10px;color:var(--text)}
.call strong{display:block;font-family:"Montserrat",sans-serif;font-weight:500;font-size:18px;color:var(--ink);margin-top:2px}
.search{position:absolute;left:930px;top:22px;width:138px;height:32px;border:1px solid var(--line);font-size:10px;color:#777;padding:9px 10px}
.search svg{position:absolute;right:9px;top:8px}
.main-nav{position:absolute;top:75px;left:570px;display:flex;font-family:"Montserrat",sans-serif;font-weight:600;font-size:11.5px;color:var(--ink)}
.main-nav a{display:block;padding:4px 10px;color:inherit;text-decoration:none;margin-right:18px}
.main-nav a.active{background:var(--blue);color:var(--white)}
.main-nav a:last-child{margin-right:0}

/* hero */
.hero{position:absolute;left:0;top:108px;width:1200px;height:517px;background:linear-gradient(90deg,#3a3a40 0%,#6b5848 35%,#8a6a4a 55%,#4a4a4e 80%,#2f3236 100%)}
.hero-shade{position:absolute;inset:0;background:linear-gradient(180deg,rgba(0,0,0,.15),rgba(0,0,0,.35))}
.hero-title{position:absolute;top:188px;width:100%;text-align:center;font-family:"Open Sans",sans-serif;font-weight:700;font-size:40px;color:var(--white);text-shadow:0 2px 4px rgba(0,0,0,.4)}
.hero-sub{position:absolute;top:236px;width:100%;text-align:center;font-size:21px;color:var(--white)}
.btn-solid{position:absolute;background:var(--blue);color:var(--white);font-family:"Open Sans",sans-serif;font-weight:700;font-size:16px;text-align:center}
.hero .btn-solid{left:525px;top:290px;width:150px;height:42px;line-height:42px}
.dots{position:absolute;top:446px;left:550px;display:flex;gap:17px;align-items:center}
.dots span{width:10px;height:10px;border-radius:50%;background:var(--white)}
.dots span.on{width:14px;height:14px;border:3px solid var(--white);background:var(--blue)}

/* section headings */
.sec-title{position:absolute;width:100%;text-align:center;font-family:"Open Sans",sans-serif;font-weight:700;font-size:19px;color:var(--ink)}
.rule{position:absolute;left:575px;width:50px;height:3px;background:var(--blue)}

/* products */
.product{position:absolute;width:303px;height:240px;overflow:hidden}
.product .bar{position:absolute;left:0;bottom:0;width:100%;height:32px;background:rgba(31,111,176,.82);color:var(--white);font-family:"Open Sans",sans-serif;font-weight:700;font-size:15px;line-height:32px;padding-left:13px}
.product .bar svg{position:absolute;right:14px;top:10px}

/* welcome band */
.welcome{position:absolute;left:0;top:1310px;width:1200px;height:485px;background:linear-gradient(180deg,#2b95d7,#2489cc)}
.welcome .sec-title,.welcome .rule{}
.welcome-copy{position:absolute;left:400px;top:128px;width:400px;text-align:center;font-size:12.5px;line-height:18px;color:var(--white)}
.feature{position:absolute;top:270px;width:260px;height:72px}
.feature .icon{position:absolute;left:0;top:0;width:72px;height:72px;border-radius:50%;background:var(--white);display:flex;align-items:center;justify-content:center}
.feature h3{position:absolute;left:86px;top:6px;font-family:"Open Sans",sans-serif;font-weight:700;font-size:12.5px;color:var(--white)}
.feature p{position:absolute;left:86px;top:26px;width:170px;font-size:11.5px;line-height:14px;color:var(--white)}
.btn-outline{position:absolute;border:2px solid currentColor;font-family:"Open Sans",sans-serif;font-weight:600;font-size:13.5px;text-align:center}
.welcome .btn-outline{left:538px;top:398px;width:123px;height:36px;line-height:32px;color:var(--white)}

/* installation */
.install-photo{position:absolute;left:544px;top:1854px;width:524px;height:372px;background:linear-gradient(120deg,#e8ecef 0%,#cfd6dc 40%,#8a939c 70%,#d9dde0 100%)}
.install-card{position:absolute;left:130px;top:1877px;width:450px;height:331px;background:var(--white);box-shadow:0 0 16px rgba(0,0,0,.18)}
.install-card h2{position:absolute;top:46px;width:100%;text-align:center;font-family:"Open Sans",sans-serif;font-weight:700;font-size:19px;color:var(--ink)}
.install-card .rule{left:200px;top:87px}
.install-card p{position:absolute;left:100px;top:122px;width:250px;text-align:center;font-size:12.5px;line-height:18px;color:var(--text)}
.install-card .btn-outline{left:164px;top:250px;width:123px;height:36px;line-height:32px;color:var(--blue);font-weight:400}

/* newsletter */
.field{position:absolute;top:2375px;height:39px;border:1px solid #bdbdbd;font-size:11px;color:#444;padding:13px 16px}
.newsletter .btn-solid{left:790px;top:2375px;width:106px;height:39px;line-height:39px;font-size:15px}

/* footer */
.site-footer{position:absolute;left:0;top:2472px;width:1200px;height:319px;background:var(--footer)}
.site-footer .brand{left:135px;top:66px}
.foot-col{position:absolute;top:64px}
.foot-col h4{font-family:"Open Sans",sans-serif;font-weight:700;font-size:12px;color:var(--ink);margin-bottom:18px}
.social{display:flex;align-items:center;gap:12px;font-size:11.5px;color:var(--text);margin-bottom:12px}
.social span.dot{width:27px;height:27px;border-radius:50%;background:var(--navy)}
.menu-list{list-style:none;font-size:11px;line-height:17.5px;color:var(--text)}
.contact-row{display:flex;gap:12px;font-size:11px;line-height:16px;color:var(--text);margin-bottom:18px}
.contact-row svg{flex:none;margin-top:2px}
.foot-rule{position:absolute;left:130px;top:238px;width:938px;height:1px;background:#c6c6c6}
.copyright{position:absolute;top:274px;width:100%;text-align:center;font-size:10.5px;color:var(--text)}
</style>
</head>
<body>

<header class="site-header">
  <div class="brand"><span class="brand-mark"></span><span class="brand-name">CLEARVALE</span></div>
  <div class="call">
    <svg width="22" height="22" viewBox="0 0 24 24"><path fill="#1f6fb0" d="M6.6 10.8a15 15 0 0 0 6.6 6.6l2.2-2.2a1 1 0 0 1 1-.25 11.4 11.4 0 0 0 3.6.57 1 1 0 0 1 1 1V20a1 1 0 0 1-1 1A17 17 0 0 1 3 4a1 1 0 0 1 1-1h3.5a1 1 0 0 1 1 1c0 1.25.2 2.45.57 3.6a1 1 0 0 1-.25 1z"/></svg>
    <div><small>Call Us</small><strong>555.014.2290</strong></div>
  </div>
  <div class="search">SEARCH
    <svg width="13" height="13" viewBox="0 0 14 14"><circle cx="5.5" cy="5.5" r="4.3" fill="none" stroke="#888" stroke-width="1.4"/><path d="M8.8 8.8l4 4" stroke="#888" stroke-width="1.5"/></svg>
  </div>
  <nav class="main-nav">
    <a class="active" href="#">HOME</a><a href="#">ABOUT US</a><a href="#">GLASS</a><a href="#">HARDWARE</a><a href="#">BLOG</a><a href="#">CONTACT US</a>
  </nav>
</header>

<section class="hero">
  <div role="img" aria-label="Modern living room seen through large dark-framed glass sliding doors" class="abs" style="inset:0"></div>
  <div class="hero-shade"></div>
  <h1 class="hero-title">GLASS &amp; HARDWARES</h1>
  <p class="hero-sub">selling all kinds of glass &amp; accessories</p>
  <a class="btn-solid">READ MORE</a>
  <div class="dots"><span></span><span></span><span class="on"></span><span></span><span></span></div>
</section>

<section class="products">
  <h2 class="sec-title" style="top:670px">OUR PRODUCTS</h2>
  <div class="rule" style="top:706px"></div>

  <div class="product" style="left:130px;top:753px">
    <div role="img" aria-label="Dark framed glass doors" class="abs" style="inset:0;background:linear-gradient(135deg,#2c3a4c,#6f8196 50%,#2a3440)"></div>
    <div class="bar">GLASS<svg width="8" height="12" viewBox="0 0 8 12"><path d="M1 1l5 5-5 5" stroke="#fff" stroke-width="2" fill="none"/></svg></div>
  </div>
  <div class="product" style="left:449px;top:753px">
    <div role="img" aria-label="Kitchen with mirrored wall panels" class="abs" style="inset:0;background:linear-gradient(160deg,#c9cdd1,#8e949a 55%,#6a5e55)"></div>
    <div class="bar">MIRROR<svg width="8" height="12" viewBox="0 0 8 12"><path d="M1 1l5 5-5 5" stroke="#fff" stroke-width="2" fill="none"/></svg></div>
  </div>
  <div class="product" style="left:765px;top:753px">
    <div role="img" aria-label="White kitchen with glass splash back" class="abs" style="inset:0;background:linear-gradient(160deg,#d6d8da,#eeeeee 50%,#9a9a9a)"></div>
    <div class="bar">SPLASH BACK<svg width="8" height="12" viewBox="0 0 8 12"><path d="M1 1l5 5-5 5" stroke="#fff" stroke-width="2" fill="none"/></svg></div>
  </div>
  <div class="product" style="left:130px;top:1007px">
    <div role="img" aria-label="Glass pool fence at dusk beside a lit house" class="abs" style="inset:0;background:linear-gradient(180deg,#1e3f8a,#3b6fc0 40%,#c89a3c 70%,#1f3f5c)"></div>
    <div class="bar">POOL FENCE<svg width="8" height="12" viewBox="0 0 8 12"><path d="M1 1l5 5-5 5" stroke="#fff" stroke-width="2" fill="none"/></svg></div>
  </div>
  <div class="product" style="left:449px;top:1007px">
    <div role="img" aria-label="Glass balustrade with steel rail" class="abs" style="inset:0;background:linear-gradient(160deg,#7e8a82,#b9c3bd 45%,#4f5a4e)"></div>
    <div class="bar">BALUSTRADE<svg width="8" height="12" viewBox="0 0 8 12"><path d="M1 1l5 5-5 5" stroke="#fff" stroke-width="2" fill="none"/></svg></div>
  </div>
  <div class="product" style="left:765px;top:1007px">
    <div role="img" aria-label="Dark lever door handle" class="abs" style="inset:0;background:radial-gradient(circle at 45% 45%,#5a6470,#c4cbd2 60%,#e1e4e7)"></div>
    <div class="bar">HARDWARE<svg width="8" height="12" viewBox="0 0 8 12"><path d="M1 1l5 5-5 5" stroke="#fff" stroke-width="2" fill="none"/></svg></div>
  </div>
</section>

<section class="welcome">
  <h2 class="sec-title" style="top:50px;color:var(--white)">WELCOME TO OUR SITE</h2>
  <div class="rule" style="top:84px;background:var(--white)"></div>
  <p class="welcome-copy">There are many variations of passages of Lorem Ipsum available, but the majority have suffered alteration in some form, by injected humour, or randomised words which don't look even slightly believable. If you are going to use a passage of Lorem Ipsum, you need to be sure there isn't anything embarrassing</p>

  <div class="feature" style="left:132px">
    <div class="icon"><svg width="34" height="34" viewBox="0 0 34 34"><rect x="3" y="3" width="28" height="28" fill="none" stroke="#2a93d5" stroke-width="3"/><path d="M17 3v28" stroke="#2a93d5" stroke-width="3"/></svg></div>
    <h3>BEST PRODUCTS</h3><p>There are many variations of passages of Lorem Ipsum available,</p>
  </div>
  <div class="feature" style="left:476px">
    <div class="icon"><svg width="34" height="34" viewBox="0 0 34 34"><path d="M5 18l8 8 16-17" fill="none" stroke="#2a93d5" stroke-width="4"/></svg></div>
    <h3>QUALITY</h3><p>There are many variations of passages of Lorem Ipsum available,</p>
  </div>
  <div class="feature" style="left:827px">
    <div class="icon"><svg width="34" height="34" viewBox="0 0 34 34"><path d="M6 22v-5a11 11 0 0 1 22 0v5" fill="none" stroke="#2a93d5" stroke-width="3"/><rect x="4" y="19" width="6" height="10" fill="#2a93d5"/><rect x="24" y="19" width="6" height="10" fill="#2a93d5"/></svg></div>
    <h3>SUPPORT</h3><p>There are many variations of passages of Lorem Ipsum available,</p>
  </div>

  <a class="btn-outline">READ MORE</a>
</section>

<section class="installation">
  <div class="install-photo" role="img" aria-label="Two installers fitting a white-framed window"></div>
  <div class="install-card">
    <h2>EXPERT INSTALLATION</h2>
    <div class="rule"></div>
    <p>There are many variations of passages of Lorem Ipsum available, but the majority have suffered alteration in some form, by injected humour, or randomised words which don't look even slightly believable.</p>
    <a class="btn-outline">READ MORE</a>
  </div>
</section>

<section class="newsletter">
  <h2 class="sec-title" style="top:2290px">NEWSLETTER SIGNUP</h2>
  <div class="rule" style="top:2332px"></div>
  <div class="field" style="left:315px;width:225px">Name</div>
  <div class="field" style="left:552px;width:226px">E mail id</div>
  <a class="btn-solid">SIGNUP</a>
</section>

<footer class="site-footer">
  <div class="brand"><span class="brand-mark"></span><span class="brand-name">CLEARVALE</span></div>

  <div class="foot-col" style="left:547px">
    <h4>FOLLOW US</h4>
    <div class="social"><span class="dot"></span>Friendlink</div>
    <div class="social"><span class="dot"></span>Chirpline</div>
    <div class="social"><span class="dot"></span>Workweave</div>
  </div>

  <div class="foot-col" style="left:752px">
    <h4>MENU</h4>
    <ul class="menu-list"><li>HOME</li><li>ABOUT US</li><li>GLASS</li><li>HARDWARE</li><li>BLOG</li><li>CONTACT US</li></ul>
  </div>

  <div class="foot-col" style="left:929px">
    <h4>CONTACT US</h4>
    <div class="contact-row"><svg width="9" height="12" viewBox="0 0 10 14"><path d="M5 0a5 5 0 0 1 5 5c0 4-5 9-5 9S0 9 0 5a5 5 0 0 1 5-5z" fill="#333"/><circle cx="5" cy="5" r="1.8" fill="#e7e7e9"/></svg><span>18 Harbour Lane<br>Brookfield, IL 60513</span></div>
    <div class="contact-row"><svg width="10" height="10" viewBox="0 0 24 24"><path fill="#333" d="M6.6 10.8a15 15 0 0 0 6.6 6.6l2.2-2.2a1 1 0 0 1 1-.25 11.4 11.4 0 0 0 3.6.57 1 1 0 0 1 1 1V20a1 1 0 0 1-1 1A17 17 0 0 1 3 4a1 1 0 0 1 1-1h3.5a1 1 0 0 1 1 1c0 1.25.2 2.45.57 3.6a1 1 0 0 1-.25 1z"/></svg><span>555.014.2290</span></div>
    <div class="contact-row"><svg width="12" height="9" viewBox="0 0 12 9"><rect width="12" height="9" fill="#333"/><path d="M0 0l6 5 6-5" stroke="#e7e7e9" fill="none"/></svg><span>info@clearvale.com</span></div>
  </div>

  <div class="foot-rule"></div>
  <p class="copyright">Copyrights @ 2018 All Rights Reserved</p>
</footer>

</body>
</html>
```